Ridgeline Haul Carriers - Website

A clean, not cluttered informative website for our business. We specialize in the transportation of radioactive materials across North America. The site is mostly for information about our company and will not be used to attract business but will be used to attract employee's mainly drivers. Driver's are very hard to find in our area. One of the pages needs to be a job's posting page with an apply now button. Either an application can be filled out there or a resume can be uploaded which ever functionality works better. I would like a website that I can easily edit, ability to change text and photos.

Number of Pages Required

5+ page

Colors

Designer to choose colors to be used in the design.

Requirements
Must have
• Home - About - Services - Jobs - Contact pages
• A way prospective employee's can apply or upload their resume to be emailed to me
• Very clean apperance
Should not have
• I don't want it to be busy

```html
<!DOCTYPE html>
<html lang="en">
<head>
<meta charset="utf-8">
<title>Ridgeline Haul Carriers</title>
<link href="https://fonts.googleapis.com/css2?family=Montserrat:wght@500;600;700&family=Open+Sans:ital,wght@0,400;0,600;0,700;1,400&display=swap" rel="stylesheet">
<style>
:root{
  --orange:#f47d16;
  --orange-dark:#e86f0c;
  --ink:#1c1c1c;
  --body:#4a4a4a;
  --muted:#8a8a8a;
  --white:#ffffff;
  --footer:#0d0d0d;
  --footer-text:#a9a9a9;
  --line:#d9d9d9;
}
*{box-sizing:border-box;margin:0;padding:0}
html,body{width:1200px;height:3673px;overflow:hidden}
body{position:relative;background:var(--white);font-family:"Open Sans",sans-serif;color:var(--body)}
a{text-decoration:none}
.abs{position:absolute}
h1,h2,h3{font-family:"Montserrat",sans-serif;color:var(--ink)}
.photo{position:absolute}

/* hero */
.hero{left:0;top:0;width:1200px;height:673px;background:linear-gradient(180deg,#8d9199 0%,#6e737b 40%,#3d4149 70%,#2a2c30 100%)}
.brand{font-family:"Montserrat",sans-serif;font-weight:700;color:var(--orange);display:flex;align-items:center;gap:10px;letter-spacing:.5px;white-space:nowrap}
.brand .mark{width:12px;height:12px;background:var(--orange);flex:none}
.hero-brand{left:110px;top:38px;font-size:22px}
.nav{left:568px;top:37px;width:632px;height:36px;background:var(--orange);display:flex;align-items:center;padding-left:62px}
.nav a{color:var(--white);font-weight:600;font-size:16px;width:103px}
.hero-title{left:0;top:236px;width:1200px;text-align:center;color:var(--white);font-size:66px;font-weight:700;letter-spacing:1px;line-height:1}
.hero-sub{left:0;top:304px;width:1200px;text-align:center;color:var(--white);font-size:24px}
.dots{left:550px;top:510px;display:flex;gap:12px}
.dots span{width:15px;height:15px;border:2px solid var(--white);border-radius:50%}
.dots span.on{background:var(--white)}
.hero-edge{left:0;top:540px}

/* about */
.about-title{left:110px;top:852px;font-size:44px;font-weight:600}
.about-sub{left:110px;top:908px;font-size:24px;color:var(--ink);white-space:nowrap}
.about-text{left:110px;top:980px;width:455px;font-size:13.5px;line-height:24px}
.about-text p+p{margin-top:16px}
.about-back{left:680px;top:841px;width:427px;height:303px;background:var(--orange)}
.about-photo{left:600px;top:774px;width:487px;height:353px;background:linear-gradient(180deg,#c9d6e3 0%,#a7b2b8 55%,#8a7a62 100%)}

/* services */
.services-photo{left:0;top:1273px;width:600px;height:471px;background:linear-gradient(135deg,#6f8a5a 0%,#9aa29c 45%,#c8521e 65%,#5d5f62 100%)}
.services-card{left:553px;top:1310px;width:471px;height:400px;background:var(--white);box-shadow:0 4px 18px rgba(0,0,0,.18);text-align:center;padding:32px 44px 0}
.services-card h2{font-size:44px;font-weight:600;margin-bottom:14px}
.services-card p{font-size:13px;line-height:24px}
.services-card p+p{margin-top:14px}
.btn{display:inline-block;background:var(--orange);color:var(--white);font-family:"Montserrat",sans-serif;font-weight:600;font-size:15px;letter-spacing:.5px;text-align:center}
.services-card .btn{position:absolute;left:172px;top:316px;width:127px;height:39px;line-height:39px}

/* hiring */
.hiring-band{left:0;top:1935px;width:1200px;height:183px;background:var(--orange)}
.hiring-tab{left:0;top:1856px}
.hiring-title{left:0;top:1872px;width:1200px;text-align:center;color:var(--white);font-size:40px;font-weight:600;letter-spacing:1px}
.hiring-sub{left:0;top:1926px;width:1200px;text-align:center;color:var(--white);font-size:19px}
.btn-outline{left:517px;top:2008px;width:166px;height:42px;border:2px solid var(--white);color:var(--white);text-align:center;line-height:38px;font-family:"Montserrat",sans-serif;font-size:15px;font-weight:600;letter-spacing:.5px}

/* faq + clients */
.faq-bg{left:0;top:2118px;width:1200px;height:588px;background:linear-gradient(180deg,#f2f3f4 0%,#e9ecee 55%,#d5d9dc 85%,#c9cdd0 100%)}
.faq-title{left:110px;top:2222px;font-size:44px;font-weight:600}
.faq-list{left:110px;top:2295px;width:440px;list-style:none}
.faq-item{border-bottom:1px solid var(--line);padding:10px 0 12px 26px;position:relative;font-size:14.5px;font-weight:600;color:var(--ink)}
.faq-item::before{content:"+";position:absolute;left:0;top:9px;font-size:18px;font-weight:700;color:var(--ink)}
.faq-item.open{color:var(--orange)}
.faq-item.open::before{content:"–";color:var(--orange)}
.faq-item.open p{color:var(--body);font-weight:400;font-size:13.5px;line-height:23px;margin-top:8px}
.clients-title{left:632px;top:2222px;font-size:44px;font-weight:600}
.client{left:630px;width:460px}
.client .avatar{position:absolute;left:0;top:0;width:72px;height:72px;border-radius:50%;background:linear-gradient(180deg,#c4b2a2,#7d6857)}
.client h3{position:absolute;left:96px;top:8px;font-size:17px;font-weight:600}
.client em{position:absolute;left:96px;top:36px;font-size:13px;color:var(--muted)}
.client p{position:absolute;left:0;top:84px;font-size:13.5px;line-height:24px}

/* query */
.query-title{left:114px;top:2812px;font-size:44px;font-weight:600}
.query-text{left:114px;top:2876px;width:420px;font-size:13.5px;line-height:25px}
.query-text p+p{margin-top:12px}
.footer-bg{left:0;top:3060px}
.form-card{left:642px;top:2829px;width:445px;height:465px;background:var(--white);box-shadow:0 4px 20px rgba(0,0,0,.2);border-radius:6px}
.field{position:absolute;left:51px;width:343px;height:48px;border:1px solid #b9b9b9;font-size:13px;padding:14px 16px;color:#555}
.field.msg{height:118px}
.form-card .btn{position:absolute;left:167px;top:384px;width:112px;height:40px;line-height:40px}

/* footer */
.footer-brand{left:114px;top:3230px;font-size:30px}
.footer-about{left:114px;top:3380px;width:380px;font-size:14px;line-height:25px;color:var(--footer-text)}
.social{left:114px;top:3478px;display:flex;gap:24px}
.social span{width:13px;height:13px;border-radius:50%;border:2px solid var(--footer-text)}
.footer-links{top:3378px;list-style:none;font-size:13.5px;line-height:27px;color:var(--footer-text)}
.copyright{left:0;top:3626px;width:1200px;text-align:center;font-size:12px;color:var(--footer-text)}
</style>
</head>
<body>

<!-- hero -->
<div class="abs hero photo" role="img" aria-label="Tractor trailer hauling radioactive material containers under bare trees"></div>
<div class="abs brand hero-brand"><span class="mark"></span>RIDGELINE HAUL CARRIERS</div>
<nav class="abs nav"><a href="#">Home</a><a href="#">About</a><a href="#">Services</a><a href="#">Jobs</a><a href="#">Contact</a></nav>
<h1 class="abs hero-title">RIDGELINE HAUL CARRIERS</h1>
<p class="abs hero-sub">We specialize in the transportation of radioactive materials across North America</p>
<div class="abs dots"><span class="on"></span><span></span><span></span><span></span></div>
<svg class="abs hero-edge" width="1200" height="135" viewBox="0 0 1200 135">
  <polygon points="0,70 340,40 600,115 900,20 1200,90 1200,135 0,135" fill="var(--orange)"/>
  <polygon points="0,100 340,40 600,135 900,20 1200,125 1200,135 0,135" fill="var(--white)"/>
</svg>

<!-- about -->
<svg class="abs" style="left:311px;top:776px" width="160" height="160" viewBox="0 0 160 160">
  <polyline points="4,52 4,4 115,4 156,45 156,156 84,156" fill="none" stroke="var(--orange)" stroke-width="8"/>
</svg>
<h2 class="abs about-title">ABOUT US</h2>
<p class="abs about-sub">Ridgeline Haul Carriers</p>
<div class="abs about-text">
  <p>Ridgeline Haul Carriers has been providing quality transportation services since our founding in 1999.</p>
  <p>Ridgeline Haul Carriers is part of the With a firm commitment to superior service and integrity above all, the RH team has developed an enviable reputation within the transportation industry</p>
</div>
<div class="abs about-back"></div>
<div class="abs about-photo photo" role="img" aria-label="White truck with a flatbed trailer parked on a gravel lot"></div>

<!-- services -->
<div class="services-photo photo" role="img" aria-label="Orange semi truck with a silver trailer on a highway"></div>
<svg class="abs" style="left:921px;top:1259px" width="160" height="160" viewBox="0 0 160 160">
  <polyline points="4,52 4,4 115,4 156,45 156,156 36,156" fill="none" stroke="var(--orange)" stroke-width="8"/>
</svg>
<div class="abs services-card">
  <h2>OUR SERVICES</h2>
  <p>At Ridgeline Haul Carriers, we specialize in both expedited and regular LTL, Partial Load and Full Truck Load service between Canada, the USA, and Mexico.</p>
  <p>In addition, to meet our just in time door to door service requirements, our policy includes one line hauls right to your delivery, which eliminates extra handling of your products which also in turn reduces damages and claims.</p>
  <a class="btn" href="#">READ MORE</a>
</div>

<!-- hiring -->
<svg class="abs hiring-tab" width="1200" height="80" viewBox="0 0 1200 80">
  <polygon points="265,0 930,0 955,80 245,80" fill="var(--orange)"/>
</svg>
<div class="abs hiring-band"></div>
<h2 class="abs hiring-title">CURRENTLY HIRING</h2>
<p class="abs hiring-sub">Freight Sales Agents Check out our employment area</p>
<a class="abs btn-outline" href="#">APPLY NOW</a>

<!-- faq & clients -->
<div class="abs faq-bg photo" role="img" aria-label="Faded highway landscape with a truck under a pale sky"></div>
<h2 class="abs faq-title">FAQ</h2>
<ul class="abs faq-list">
  <li class="faq-item open">Lorem ipsum dolor sit amet, consectetur adipiscing ?
    <p>Sed ut perspiciatis unde omnis iste natus error sit voluptatem accusantium doloremque laudantium, totam rem aperiam, eaque ipsa quae ab illo inventore veritatis et quasi architecto...</p></li>
  <li class="faq-item" style="padding-top:20px">Lorem ipsum dolor sit amet, consectetur adipiscing ?</li>
  <li class="faq-item" style="padding-top:20px">Lorem ipsum dolor sit amet, consectetur adipiscing ?</li>
  <li class="faq-item" style="border:0;padding-top:14px">Lorem ipsum dolor sit amet, consectetur adipiscing ?</li>
</ul>
<h2 class="abs clients-title">CLIENT SAY'S</h2>
<div class="abs client" style="top:2302px">
  <div class="avatar" role="img" aria-label="Client portrait"></div>
  <h3>Dana Whitlow</h3><em>Lorem ipsum dolor sit amet.</em>
  <p>Lorem ipsum dolor sit amet, consectetur adipiscing elit, sed do eiusmod tempor incididunt ut labore et dolore magna aliqua. Ut enim ad minim</p>
</div>
<div class="abs client" style="top:2462px">
  <div class="avatar" role="img" aria-label="Client portrait"></div>
  <h3>Marcus Reyes</h3><em>Lorem ipsum dolor sit amet.</em>
  <p>Lorem ipsum dolor sit amet, consectetur adipiscing elit, sed do eiusmod tempor incididunt ut labore et dolore magna aliqua. Ut enim ad minim</p>
</div>

<!-- query -->
<h2 class="abs query-title">ANY QUERY ?</h2>
<div class="abs query-text">
  <p>Lorem ipsum dolor sit amet, consectetur adipiscing elit, sed do eiusmod tempor incididunt ut labore et dolore magna aliqua.</p>
  <p>Sed ut perspiciatis unde omnis iste natus error sit voluptatem accusantium doloremque laudantium, totam rem aperiam.</p>
</div>
<svg class="abs footer-bg" width="1200" height="613" viewBox="0 0 1200 613">
  <polygon points="0,20 600,130 1200,20 1200,613 0,613" fill="var(--footer)"/>
  <polygon points="0,20 160,50 0,65" fill="var(--orange)"/>
  <polygon points="1200,20 1040,50 1200,65" fill="var(--orange)"/>
  <polygon points="0,65 160,50 600,130 1040,50 1200,65 1200,80 600,130 0,80" fill="var(--footer)"/>
</svg>
<svg class="abs" style="left:593px;top:2770px" width="160" height="160" viewBox="0 0 160 160">
  <polyline points="4,156 4,45 45,4 156,4 156,52" fill="none" stroke="var(--orange)" stroke-width="8"/>
</svg>
<form class="abs form-card">
  <div class="field" style="top:48px">Name</div>
  <div class="field" style="top:109px">Phone No</div>
  <div class="field" style="top:170px">Email</div>
  <div class="field msg" style="top:231px">Message</div>
  <span class="btn">SEND</span>
</form>

<!-- footer -->
<div class="abs brand footer-brand"><span class="mark"></span>RIDGELINE HAUL CARRIERS</div>
<p class="abs footer-about">Lorem ipsum dolor sit amet, consectetur adipiscing elit, sed do eiusmod tempor incididunt ut labore et dolore magna aliqua</p>
<div class="abs social"><span></span><span></span><span></span><span></span><span></span></div>
<ul class="abs footer-links" style="left:798px"><li>Home</li><li>About</li><li>Services</li><li>Jobs</li><li>Contact</li></ul>
<ul class="abs footer-links" style="left:977px"><li>Faq</li><li>Privacy Policy</li><li>Terms &amp; Services</li></ul>
<p class="abs copyright">© 2019 Copyrights. THE COMPANY NAME. All rights reserved.</p>

</body>
</html>
```